Business card design Needed for new logo / Construction business, home extensions and new builds

We need a business card design using our new logo files which i will attach to this project :)

We are a small construction business specialising in home extensions, new builds and property development. We are very ambitious and would appreciate professional and elegant designs for our new business card.

Very serious about using the services on MakerQuarry and recently acquired our new logo from here :)

Please get involved, i will feedback when i can as i am very busy but can respond daily, thanks

Target Market(s)

People that want to build onto their houses, new building developments or adding too their existing property

Industry/Entity Type

Construction

Contact Information for Business Card

Renwick Tolliver Construction, Lionel Ashby (Managing Director), Tel 07822254961, email - info@renwick-tolliver, www.renwick-tolliver.co.uk

Colors

Designer to choose colors to be used in the design.

Requirements
Must have
• I like a deep grey on the back please. A lot of you have provided black from and back, try mixing things up a little. The black looks cool 😎 Thanks

```html
<!DOCTYPE html>
<html lang="en">
<head>
<meta charset="utf-8">
<title>Renwick Tolliver Construction – Business Card</title>
<link rel="stylesheet" href="https://fonts.googleapis.com/css2?family=Open+Sans:wght@400;600;700&display=swap">
<style>
  :root {
    --page: #2b2b2e;
    --card: #1e1e22;
    --card-deep: #19191c;
    --gold: #f0b323;
    --gold-soft: #d9a441;
    --silver: #c9c9cc;
    --text: #f2f2f2;
    --emboss: #3a3a40;
    --rule: #8a8a8f;
  }
  * { box-sizing: border-box; margin: 0; padding: 0; }
  html, body {
    width: 1200px; height: 780px; overflow: hidden;
    background: var(--page);
    font-family: "Open Sans", Arial, sans-serif;
  }
  .sheet {
    width: 1200px; height: 780px;
    display: flex; align-items: center; justify-content: center; gap: 60px;
  }
  .card {
    position: relative;
    width: 520px; height: 336px;
    border-radius: 26px;
    border: 3px solid var(--gold);
    overflow: hidden;
  }
  .card--front { background: var(--card); }
  .card--back { background: linear-gradient(135deg, var(--card) 0%, var(--card-deep) 100%); }

  /* front */
  .brand {
    position: absolute; inset: 0;
    display: flex; align-items: center; justify-content: center; gap: 14px;
  }
  .brand__mark { width: 22px; height: 22px; background: var(--emboss); }
  .brand__name {
    color: var(--emboss);
    font-weight: 700; font-size: 23px; letter-spacing: 1.5px;
    text-transform: uppercase; text-align: center; line-height: 1.3;
  }

  /* back */
  .person {
    position: absolute; left: 40px; top: 108px;
  }
  .person__name { font-weight: 700; font-size: 34px; line-height: 1.1; }
  .person__first { color: var(--silver); }
  .person__last { color: var(--gold-soft); }
  .person__role { color: var(--text); font-size: 15px; margin-top: 4px; }

  .divider {
    position: absolute; left: 268px; top: 80px;
    width: 1px; height: 130px;
    background: linear-gradient(to bottom, transparent, var(--rule), transparent);
  }
  .contacts {
    position: absolute; left: 290px; top: 98px;
    list-style: none; display: flex; flex-direction: column; gap: 12px;
  }
  .contacts__item {
    display: flex; align-items: center; gap: 8px;
    color: var(--text); font-size: 12.5px;
  }
  .contacts__icon { width: 14px; height: 14px; flex: none; }

  .address {
    position: absolute; left: 0; right: 0; bottom: 44px;
    text-align: center; color: var(--text); font-size: 14px;
  }
</style>
</head>
<body>
<main class="sheet">
  <section class="card card--front" aria-label="Card front">
    <div class="brand">
      <span class="brand__mark"></span>
      <span class="brand__name">Renwick Tolliver<br>Construction</span>
    </div>
  </section>

  <section class="card card--back" aria-label="Card back">
    <div class="person">
      <p class="person__name"><span class="person__first">Lionel</span> <span class="person__last">Ashby</span></p>
      <p class="person__role">Managing Director</p>
    </div>

    <div class="divider"></div>

    <ul class="contacts">
      <li class="contacts__item">
        <svg class="contacts__icon" viewBox="0 0 24 24" aria-hidden="true"><path fill="#f0b323" d="M6.6 10.8a15.1 15.1 0 0 0 6.6 6.6l2.2-2.2a1 1 0 0 1 1-.25 11.4 11.4 0 0 0 3.6.57 1 1 0 0 1 1 1V20a1 1 0 0 1-1 1A17 17 0 0 1 3 4a1 1 0 0 1 1-1h3.5a1 1 0 0 1 1 1c0 1.25.2 2.45.57 3.57a1 1 0 0 1-.25 1z"/></svg>
        0782 225 4961
      </li>
      <li class="contacts__item">
        <svg class="contacts__icon" viewBox="0 0 24 24" aria-hidden="true"><rect x="2" y="5" width="20" height="14" rx="2" fill="#f0b323"/><path d="M3 6.5l9 6.5 9-6.5" fill="none" stroke="#1e1e22" stroke-width="1.8"/></svg>
        info@renwick-tolliver.co.uk
      </li>
      <li class="contacts__item">
        <svg class="contacts__icon" viewBox="0 0 24 24" aria-hidden="true"><circle cx="12" cy="12" r="9.5" fill="none" stroke="#f0b323" stroke-width="2"/><path d="M2.5 12h19M12 2.5c3 3 3 16 0 19M12 2.5c-3 3-3 16 0 19" fill="none" stroke="#f0b323" stroke-width="1.6"/></svg>
        www.renwick-tolliver.co.uk
      </li>
    </ul>

    <p class="address">Harlow Lane, Westbridge Kelmouth, KM4 7QT</p>
  </section>
</main>
</body>
</html>
```